Larkspur Talent IT Recruiting firm needs a business card design for Recruiters, Sourcers, and Account

We need business cards that allow us to change all contact info, names, titles (Recruiter, Sourcer, Account Manager, Director, CEO, etc) per person since we have three offices, in three cities, Phoenix, Austin, and Las Vegas. We do recruiting and contractors for IT positions (Developers, Architects, Software Engineers, Security Engineers, Help Desk, DBAs, PMs, Scrum Masters, etc.) Our client companies are very diverse from Meridian 100 to silicone Valley type start-ups.

So, while we what hip, techie, and quirky, it still needs to be professional. Primary color we use is blue, with silver as a secondary color.

Target Market(s)

IT, Technology

Industry/Entity Type

Business

Contact Information for Business Card

Company name: Larkspur Talent, Inc.
Website: www.larkspurtalent.example
Logos for Careerloop, Blipster, and Myriada

Name, Title, Office Number, Cell Number, email

Font styles to use
Serif
Sans Serif

Colors
0455a3
d5d5d5

Requirements
Nice to have
• The grey I selected below is not necessary - but, would like silver included. I included a card design (File 3: LTI early trial example.jpg) that I had started on. It's very rough, and not quite what we're looking for, but what we did like is the logo, big, maybe a bit faded, off center, goes out of frame, etc. Still looking for other ideas - you are the pros! But, just an idea of a design element we liked.

```html
<!DOCTYPE html>
<html lang="en">
<head>
<meta charset="utf-8">
<title>Larkspur Talent — Business Card</title>
<link rel="stylesheet" href="https://fonts.googleapis.com/css2?family=Marcellus&family=Source+Sans+3:wght@400;600&display=swap">
<style>
  :root {
    --backdrop: #161616;
    --card-front: #ffffff;
    --card-back: #555555;
    --brand-blue: #0455a3;
    --brand-bright: #1a8ad4;
    --ink: #222222;
    --ink-soft: #444444;
    --rule: #bcbcbc;
    --silver: #d5d5d5;
    --white: #ffffff;
  }
  * { margin: 0; padding: 0; box-sizing: border-box; }
  html, body { width: 1200px; height: 907px; overflow: hidden; background: var(--backdrop); }
  .canvas { position: relative; width: 1200px; height: 907px; }

  .card { position: absolute; left: 300px; width: 600px; height: 343px; box-shadow: 0 6px 18px rgba(0,0,0,.6); overflow: hidden; }
  .card--front { top: 98px; background: var(--card-front); }
  .card--back { top: 475px; background: var(--card-back); }

  .wordmark { position: absolute; left: 0; right: 0; text-align: center; font-family: "Marcellus", serif; }
  .wordmark__name { font-size: 40px; letter-spacing: 2px; line-height: 1; }
  .wordmark__tagline { margin-top: 30px; font-size: 15px; letter-spacing: 2.4px; line-height: 1; }
  .card--front .wordmark { top: 86px; }
  .card--front .wordmark__name { color: var(--brand-blue); }
  .card--front .wordmark__tagline { color: var(--ink); }
  .card--back .wordmark { top: 130px; }
  .card--back .wordmark__name, .card--back .wordmark__tagline { color: var(--white); }

  .person { position: absolute; right: 372px; top: 221px; text-align: right; font-family: "Source Sans 3", sans-serif; }
  .person__name { font-size: 22px; color: var(--brand-blue); line-height: 1.1; }
  .person__title { font-size: 16px; color: var(--ink-soft); margin-top: 2px; }
  .divider { position: absolute; left: 247px; top: 207px; width: 1px; height: 73px; background: var(--rule); }

  .contacts { position: absolute; left: 270px; top: 199px; list-style: none; font-family: "Source Sans 3", sans-serif; font-size: 15.5px; color: var(--ink-soft); }
  .contacts li { display: flex; align-items: center; height: 22.5px; }
  .contacts svg { width: 14px; height: 14px; margin-right: 8px; fill: var(--brand-blue); flex: none; }

  .band { position: absolute; left: 0; right: 0; bottom: 0; height: 14px; background: linear-gradient(90deg, var(--brand-blue), var(--brand-bright) 55%, var(--brand-blue)); }
  .band::before { content: ""; position: absolute; left: 0; right: 0; top: -4px; height: 2px; background: #555; }

  .social { position: absolute; left: 0; right: 0; top: 289px; display: flex; justify-content: center; gap: 12px; font-family: "Source Sans 3", sans-serif; font-size: 12px; color: var(--white); }
  .social__item { display: flex; align-items: center; gap: 5px; }
  .social__item::before { content: ""; width: 26px; height: 26px; border-radius: 3px; background: var(--brand-bright); }
</style>
</head>
<body>
<main class="canvas">
  <section class="card card--front" aria-label="Card front">
    <div class="wordmark">
      <div class="wordmark__name">LARKSPUR TALENT</div>
      <div class="wordmark__tagline">HIRING FOR WHAT'S NEXT</div>
    </div>
    <div class="person">
      <div class="person__name">Dana Whitfield</div>
      <div class="person__title">Manager</div>
    </div>
    <div class="divider"></div>
    <ul class="contacts">
      <li><svg viewBox="0 0 16 16"><path d="M4 1l3 3-2 2c1 2 3 4 5 5l2-2 3 3-2 3C7 15 1 9 1 3z"/></svg>555-207-8814</li>
      <li><svg viewBox="0 0 16 16"><path d="M4 0h8v16H4zM5.5 2v6h5V2zM5.5 10v1h1v-1zm2 0v1h1v-1zm2 0v1h1v-1zM5.5 12v1h1v-1zm2 0v1h1v-1zm2 0v1h1v-1z"/></svg>555-361-9027</li>
      <li><svg viewBox="0 0 16 16"><path d="M1 3h14v10H1zM2 4.5v.6l6 4 6-4v-.6L8 8.4z"/></svg>info@larkspurtalent.example</li>
      <li><svg viewBox="0 0 16 16"><path d="M8 1a7 7 0 100 14A7 7 0 008 1zm0 1.3c.8.8 1.4 2.2 1.6 4.2H6.4C6.6 4.5 7.2 3.1 8 2.3zM2.4 7.5h2.7c0 1.1.2 2.1.5 3H3.2a5.7 5.7 0 01-.8-3zm0-1a5.7 5.7 0 01.8-2.4h2.4c-.3.7-.5 1.5-.5 2.4zm8.5 1h2.7a5.7 5.7 0 01-.8 3h-2.4c.3-.9.5-1.9.5-3zm0-1c0-.9-.2-1.7-.5-2.4h2.4c.4.7.7 1.5.8 2.4zM6.4 7.5h3.2c0 1.1-.2 2.1-.5 3H6.9c-.3-.9-.5-1.9-.5-3zm.8 4h1.6c-.2.9-.5 1.6-.8 2.2-.3-.6-.6-1.3-.8-2.2z"/></svg>www.larkspurtalent.example</li>
    </ul>
    <div class="band"></div>
  </section>

  <section class="card card--back" aria-label="Card back">
    <div class="wordmark">
      <div class="wordmark__name">LARKSPUR TALENT</div>
      <div class="wordmark__tagline">HIRING FOR WHAT'S NEXT</div>
    </div>
    <div class="social">
      <span class="social__item">Careerloop</span>
      <span class="social__item">Blipster</span>
      <span class="social__item">Myriada</span>
    </div>
  </section>
</main>
</body>
</html>
```